House Cleaning Platform for Consumers and Cleaners

UPDATE: I've attached screenshots showing a purchase flow example, something all designers have missed in their designs. PLEASE check the URLs I've included in the brief for examples of a cleaning website. I've seen mostly landing pages and nothing else.

WHAT I'M LOOKING FOR:
I need the UI designed for a house cleaning web platform from 2 separate experiences: one from the consumer end to order a cleaner to come clean their house and one from a cleaner’s end that manages their orders and manages their schedule.

The UI will need to include photo uploading for before and after photos, a checkout/cart experience w/ tips, toggle options for adding and removing rooms/extras cleaning add-ons, customer+cleaner reviews (meaning the cleaner finished the job and they can rate and review the customer as well as the customer can rate and review the cleaner), order history for consumers, job history for cleaners, profile, settings, and landing pages for both.

PLEASE DO NOT USE THE COLOR BLUE AS THE PRIMARY COLOR. Use a light green (HEX #2fdf86) instead for primary theming color.

REFERENCES:
If you'd like a few websites I've enjoyed for references, checkout:
larkpolish.example, vomby.example, and brightfernhome.example.

For sake of branding, the company name is PlumNest. Currently do not have a logo as we have not decided on the name. Logo will come later.

Feel free to reach out to me if you have any questions!
Updates

Most designer submissions were a landing page and only a landing page. Very few designed the flows I requested and none designed a schedule management page. I even updated the Brief to more clearly outline the needs and references. Only about 2-3 of the designers actually did more than a landing page. Still don't believe I received 6 designers input that I had paid for.

Target Market(s)

FULL-TIME WORKING HOUSEHOLDS, SINGLE PROFESSIONALS, SINGLE PARENTS, ELDERLY & MOBILITY CHALLENGED, BUSY BODIES.

Industry/Entity Type

Cleaning, gig work.

Number of Pages Required

5+ page

Font styles to use
Other font styles liked:
• Jost or Lexend are great Google Font options I've used in the pitch deck and horribly done app mockups.

Colors
00AB8E
00BBA5
67D7C9
C6EFE9
E9F9F6
59FF00
82FF00
B8FF75
E3FFCB
F4FFEA
FFF300
FFF600
FEFA6F
FFFEC7
FFFEE8
FFC000
F8CF3A
FAE287
FDF2CF
FEFAEE

Requirements
Must have
• Landing page, consumer flow, cleaner schedule management, checkout flow, Rate & Review for consumer and/or cleaner, order history, profile.
Nice to have
• I'd like it to be simple in design and modern, but not so simple it's boring. Iconography can sometimes break that up, but I don't want it looking busy. It's a cleaning platform so the UI should look clean.

```html
<!DOCTYPE html>
<html lang="en">
<head>
<meta charset="UTF-8">
<title>PlumNest – Book Your Services Now</title>
<link rel="stylesheet" href="https://fonts.googleapis.com/css2?family=Lexend:wght@400;500&family=Open+Sans:wght@400;600;700&family=Nunito:wght@400&display=swap">
<style>
  :root {
    --green: #22d07f;
    --orange: #fb8f1c;
    --ink: #111111;
    --muted: #b5b5b5;
    --border: #c9c9c9;
    --disabled: #c8c8c8;
    --white: #ffffff;
  }
  * { box-sizing: border-box; margin: 0; padding: 0; }
  html, body { width: 937px; height: 1200px; overflow: hidden; background: var(--white); }
  body { position: relative; font-family: "Open Sans", sans-serif; color: var(--ink); }
  .abs { position: absolute; }

  .brand { left: 80px; top: 14px; font-family: "Open Sans", sans-serif; font-weight: 700; font-size: 24px; color: var(--green); letter-spacing: -0.3px; }
  .nav a { position: absolute; top: 21px; font-family: "Lexend", sans-serif; font-size: 9.4px; color: var(--ink); text-decoration: none; }
  .search { left: 571px; top: 18px; width: 170px; height: 19px; border: 1px solid #dddddd; border-radius: 10px; font-family: "Lexend", sans-serif; font-size: 9px; padding-left: 31px; line-height: 17px; }
  .search svg { position: absolute; left: 5px; top: 3px; }
  .login { left: 766px; top: 21px; font-family: "Lexend", sans-serif; font-size: 9.4px; }
  .signup { left: 800px; top: 18px; width: 58px; height: 19px; border-radius: 10px; background: var(--green); font-family: "Lexend", sans-serif; font-size: 8px; text-align: center; line-height: 19px; }

  .page-title { left: 0; width: 937px; top: 98px; text-align: center; font-weight: 700; font-size: 29px; }
  .rule { left: 0; top: 167px; width: 937px; height: 1px; background: var(--green); opacity: .6; }

  .section-title { left: 80px; font-weight: 600; font-size: 15.5px; }
  .hint { left: 80px; top: 251px; font-family: "Nunito", sans-serif; font-size: 9px; color: #333; }
  .label { font-size: 10.4px; }
  .field { border: 1px solid var(--border); border-radius: 2px; height: 29px; font-family: "Nunito", sans-serif; font-size: 9px; color: var(--muted); padding-left: 14px; line-height: 27px; }
  .field.filled { color: var(--ink); }
  .date-part { display: inline-block; padding-right: 4px; margin-right: 4px; border-right: 1px solid var(--border); line-height: 14px; }
  .date-part:last-of-type { border-right: none; }
  .field svg { position: absolute; }
  .apply { position: absolute; left: 271px; top: 4px; width: 80px; height: 19px; border-radius: 2px; font-family: "Lexend", sans-serif; font-weight: 500; font-size: 9px; text-align: center; line-height: 19px; }
  .apply.active { background: var(--orange); color: var(--ink); }
  .apply.idle { background: var(--disabled); color: var(--white); }

  .btn { top: 1089px; width: 136px; height: 39px; border-radius: 20px; font-family: "Lexend", sans-serif; font-weight: 500; font-size: 12px; text-align: center; line-height: 39px; }
  .btn.back { left: 80px; border: 1px solid var(--border); }
  .btn.next { left: 240px; background: var(--green); }
</style>
</head>
<body>
  <div class="abs brand">PlumNest</div>
  <nav class="nav">
    <a style="left:343px">Home</a>
    <a style="left:383px">Pricing</a>
    <a style="left:427px">Services</a>
    <a style="left:478px">Contact</a>
    <a style="left:526px">Help</a>
  </nav>
  <div class="abs search">
    <svg width="12" height="12" viewBox="0 0 12 12"><circle cx="5" cy="5" r="4" fill="none" stroke="#333" stroke-width="1"/><line x1="8" y1="8" x2="11" y2="11" stroke="#333" stroke-width="1"/></svg>
    Search
  </div>
  <div class="abs login">Login</div>
  <div class="abs signup">Sign Up</div>

  <h1 class="abs page-title">Book Your Services Now</h1>
  <div class="abs rule"></div>

  <h2 class="abs section-title" style="top:218px">Date Of Cleaning</h2>
  <p class="abs hint">Choose from available appointment times. Please note there is a 1-hour arrival window.</p>
  <div class="abs field" style="left:80px;top:279px;width:366px">
    <span class="date-part">DD</span><span class="date-part">MM</span><span class="date-part">YYYY</span>
    <svg style="left:339px;top:8px" width="11" height="11" viewBox="0 0 11 11"><rect x="1" y="2" width="9" height="8" rx="1" fill="none" stroke="#333" stroke-width=".9"/><line x1="1" y1="4.5" x2="10" y2="4.5" stroke="#333" stroke-width=".9"/><line x1="3.5" y1="0.5" x2="3.5" y2="2.5" stroke="#333" stroke-width=".9"/><line x1="7.5" y1="0.5" x2="7.5" y2="2.5" stroke="#333" stroke-width=".9"/></svg>
  </div>

  <h2 class="abs section-title" style="top:348px">Address Details</h2>
  <div class="abs label" style="left:80px;top:387px">Property Address</div>
  <div class="abs label" style="left:492px;top:387px">Apartment Or Suite #</div>
  <div class="abs field" style="left:80px;top:411px;width:366px">Property Address</div>
  <div class="abs field" style="left:492px;top:411px;width:366px">Apartment Or Suite #</div>

  <div class="abs label" style="left:80px;top:456px">City</div>
  <div class="abs label" style="left:355px;top:456px">State</div>
  <div class="abs label" style="left:630px;top:456px">Zip Code</div>
  <div class="abs field" style="left:80px;top:480px;width:228px">City</div>
  <div class="abs field" style="left:355px;top:480px;width:228px">State</div>
  <div class="abs field" style="left:630px;top:480px;width:228px">Zip Code</div>

  <div class="abs label" style="left:80px;top:525px">Notes Or Special Instructions?</div>
  <div class="abs field" style="left:80px;top:550px;width:778px;height:88px;line-height:normal;padding-top:8px">Notes Or Special Instructions?</div>

  <h2 class="abs section-title" style="top:677px">Contact Information</h2>
  <div class="abs label" style="left:80px;top:716px">First Name</div>
  <div class="abs label" style="left:492px;top:716px">Last Name</div>
  <div class="abs field" style="left:80px;top:740px;width:366px">First Name</div>
  <div class="abs field" style="left:492px;top:740px;width:366px">Last Name</div>
  <div class="abs label" style="left:80px;top:785px">Email</div>
  <div class="abs label" style="left:492px;top:785px">Phone</div>
  <div class="abs field" style="left:80px;top:809px;width:366px">Email</div>
  <div class="abs field" style="left:492px;top:809px;width:366px">Phone</div>

  <h2 class="abs section-title" style="top:878px">Other Details</h2>
  <div class="abs label" style="left:80px;top:917px">How Did You Hear About Us?</div>
  <div class="abs field" style="left:80px;top:941px;width:778px">
    How Did You Hear About Us?
    <svg style="left:753px;top:11px" width="10" height="6" viewBox="0 0 10 6"><polygon points="0,0 10,0 5,6" fill="#111"/></svg>
  </div>

  <div class="abs label" style="left:80px;top:986px">Enter Coupon Code</div>
  <div class="abs label" style="left:492px;top:986px">Enter Coupon Code</div>
  <div class="abs field filled" style="left:80px;top:1010px;width:366px">12345<span class="apply active">Apply</span></div>
  <div class="abs field" style="left:492px;top:1010px;width:366px">Enter Coupon Code<span class="apply idle">Apply</span></div>

  <div class="abs btn back">Back</div>
  <div class="abs btn next">Save &amp; Next</div>
</body>
</html>
```